Velk Partners Building Business Cards

We need a business card that reflects our business as "Solar Experts" in San Diego. Browse our website www.velkpartners.example our License needs to be displayed as "CSLB# 3867140" our phone number is (619) 555-0187

Save thousands on your electric bills and increase the value of your home while helping to protect the environment. Our solar installation experts will help you design the system that's right for you, using only the highest quality equipment that will look great and give you ideal performance. Our goal is to make you energy independent, and get your electric bill to 0.

Paul Osterby
(619) 555-0187
paul@velkpartners.example

Target Market(s)

Home owners in san diego looking for solar

Industry/Entity Type

Solar Energy

Contact Information for Business Card

Paul Osterby
(619) 555-0187
paul@velkpartners.example

Font styles to use
Other font styles liked:
• Use our logo font

Requirements
Must have
• License needs to be displayed as "CSLB# 3867140" our phone number is (619) 555-0187
Nice to have
• Real images of rooftop home solar in san diego
Should not have
• our business address

```html
<!DOCTYPE html>
<html lang="en">
<head>
<meta charset="utf-8">
<title>Velk Partners Building – Business Cards</title>
<link rel="stylesheet" href="https://fonts.googleapis.com/css2?family=Open+Sans:wght@400;600;700&display=swap">
<style>
  :root {
    --navy: #1b3f7a;
    --navy-deep: #173a73;
    --sun: #f6b21b;
    --sun-light: #fbd25a;
    --paper: #ffffff;
    --ink: #2b2f38;
    --stage: #e9e7e2;
  }
  * { box-sizing: border-box; margin: 0; padding: 0; }
  html, body {
    width: 1200px;
    height: 950px;
    overflow: hidden;
    background: var(--stage);
    font-family: "Open Sans", sans-serif;
  }
  .sheet {
    position: relative;
    width: 1200px;
    height: 950px;
    display: flex;
    justify-content: center;
    align-items: center;
    gap: 90px;
  }
  .card {
    position: relative;
    width: 400px;
    height: 690px;
    border-radius: 4px;
    overflow: hidden;
    box-shadow: 0 6px 20px rgba(0,0,0,0.12);
  }

  /* Front */
  .card-front { background: var(--paper); }
  .front-brand {
    position: absolute;
    top: 62px;
    right: 34px;
    font-weight: 700;
    font-size: 27px;
    line-height: 1.1;
    color: var(--navy);
    text-align: right;
    letter-spacing: -0.3px;
  }
  .contact {
    position: absolute;
    top: 170px;
    right: 44px;
    text-align: right;
    color: var(--ink);
  }
  .contact-name {
    font-weight: 700;
    font-size: 22px;
    color: var(--navy);
  }
  .contact-role {
    font-size: 15px;
    color: var(--sun);
    margin-bottom: 12px;
  }
  .contact-line {
    display: flex;
    justify-content: flex-end;
    align-items: center;
    gap: 7px;
    font-size: 14.5px;
    line-height: 24px;
  }
  .contact-line svg { width: 14px; height: 14px; flex: none; }
  .front-artwork {
    position: absolute;
    left: 0;
    bottom: 0;
    width: 340px;
    height: 290px;
    background: linear-gradient(180deg, var(--sun-light) 0%, var(--sun) 45%, var(--navy) 100%);
  }

  /* Back */
  .card-back { background: var(--navy-deep); }
  .back-brand {
    position: absolute;
    top: 300px;
    left: 0;
    right: 0;
    text-align: center;
    font-weight: 700;
    font-size: 30px;
    line-height: 1.15;
    color: var(--paper);
    letter-spacing: -0.3px;
  }
  .back-band {
    position: absolute;
    left: 0;
    right: 0;
    bottom: 74px;
    height: 44px;
    background: var(--sun);
    display: flex;
    align-items: center;
    justify-content: flex-end;
    padding-right: 30px;
    font-size: 15px;
    font-weight: 600;
    letter-spacing: 2.5px;
    color: var(--navy-deep);
  }
</style>
</head>
<body>
<main class="sheet">

  <section class="card card-front" aria-label="Business card front">
    <div class="front-brand">Velk Partners<br>Building</div>

    <div class="contact">
      <p class="contact-name">Paul Osterby</p>
      <p class="contact-role">CEO/Founder</p>
      <p class="contact-line">CSLB# 3867140</p>
      <p class="contact-line">
        <svg viewBox="0 0 16 16" aria-hidden="true"><path fill="#1b3f7a" d="M4 1.5l2.2 3-1.3 1.6a8.5 8.5 0 0 0 5 5l1.6-1.3 3 2.2-1.2 2.4C7.4 14.3 1.7 8.6 1.6 2.7z"/></svg>
        (619) 555-0187
      </p>
      <p class="contact-line">
        <svg viewBox="0 0 16 16" aria-hidden="true"><rect x="1" y="3" width="14" height="10" rx="1.5" fill="#1b3f7a"/><path d="M1.5 4l6.5 5 6.5-5" fill="none" stroke="#fff" stroke-width="1.3"/></svg>
        paul@velkpartners.example
      </p>
      <p class="contact-line">
        <svg viewBox="0 0 16 16" aria-hidden="true"><circle cx="8" cy="8" r="6.5" fill="none" stroke="#1b3f7a" stroke-width="1.5"/><ellipse cx="8" cy="8" rx="2.8" ry="6.5" fill="none" stroke="#1b3f7a" stroke-width="1.2"/><path d="M1.5 8h13" stroke="#1b3f7a" stroke-width="1.2"/></svg>
        www.velkpartners.example
      </p>
    </div>

    <div class="front-artwork" role="img" aria-label="Area for decorative artwork of a rising sun over blue waves"></div>
  </section>

  <section class="card card-back" aria-label="Business card back">
    <div class="back-brand">Velk Partners<br>Building</div>
    <div class="back-band">www.velkpartners.example</div>
  </section>

</main>
</body>
</html>
```